Corvane Paintless Dent Removal

Our company works on vehicles removing dents using a highly skilled trade which the metal is massaged out with special tools without disturbing the original paint, hence paintless dent removal. Besides keeping the paint and metal original its also very environmentally friendly since no paint or toxic fillers are used. Also we we are one of the most experienced companies in the business with 25 years

Target Market(s)

Retail Automobile consumers, Auto Dealerships and Auto Body Shops

Industry/Entity Type

Auto Repair

Contact Information for Business Card

Dale Hollister
PO Box 518 Brookmere, NY 11962
631-555-0148
corvanepdr@mailbox-example.com
website corvanepdr.example
vidstream corvane paintless dent removal
25 years of experience removing Dents, Dings and Hail Damage

Font styles to use
Serif
Sans Serif

Colors

Designer to choose colors to be used in the design.

Requirements
Must have
• I do like things that are simple but classy and somewhat bold, also I like my logo so that should be somewhat important

```html
<!DOCTYPE html>
<html lang="en">
<head>
<meta charset="utf-8">
<title>Corvane Paintless Dent Removal – Business Card</title>
<link href="https://fonts.googleapis.com/css2?family=Fira+Sans:wght@400;500;700;800&display=swap" rel="stylesheet">
<style>
  :root {
    --navy: #12284c;
    --green: #7dc242;
    --white: #ffffff;
    --ink: #1c2433;
    --stage: #262626;
  }
  * { margin: 0; padding: 0; box-sizing: border-box; }
  html, body { width: 1200px; height: 930px; overflow: hidden; }
  body {
    background: var(--stage);
    font-family: "Fira Sans", sans-serif;
    position: relative;
  }
  .card {
    position: absolute;
    left: 278px;
    width: 645px;
    height: 368px;
    border-radius: 18px;
    overflow: hidden;
  }
  .card--front { top: 76px; background: var(--white); }
  .card--back { top: 486px; background: var(--navy); }

  .front-waves { position: absolute; inset: 0; }

  .holder { position: absolute; right: 35px; top: 38px; text-align: right; }
  .holder__name {
    color: var(--white); font-weight: 500; font-size: 25px; letter-spacing: 1px;
  }
  .holder__role { color: var(--green); font-size: 16px; margin-top: 1px; }

  .brand {
    position: absolute; display: flex; align-items: center; gap: 10px;
  }
  .brand__dot { border-radius: 50%; flex: none; }
  .brand__name { font-weight: 800; line-height: 1.05; text-transform: uppercase; }

  .card--front .brand { left: 33px; top: 134px; }
  .card--front .brand__dot { width: 22px; height: 22px; background: var(--green); }
  .card--front .brand__name { color: var(--navy); font-size: 21px; }

  .divider {
    position: absolute; left: 33px; right: 35px; top: 254px;
    border-top: 1.5px solid var(--navy);
  }
  .contacts {
    position: absolute; left: 33px; top: 279px; list-style: none;
    color: var(--ink); font-size: 16px; line-height: 20.5px;
  }
  .contacts li { display: flex; align-items: center; gap: 8px; }
  .contacts svg { width: 10px; height: 10px; flex: none; }
  .address {
    position: absolute; right: 35px; top: 299.5px; text-align: right;
    color: var(--ink); font-size: 16px; line-height: 20.5px; font-style: normal;
  }

  .card--back .brand { left: 0; right: 0; top: 150px; justify-content: center; }
  .card--back .brand__dot { width: 32px; height: 32px; background: var(--green); }
  .card--back .brand__name { color: var(--white); font-size: 30px; text-align: left; }

  .tagline {
    position: absolute; left: 0; right: 0; top: 300px; text-align: center;
    color: var(--white); font-size: 17px; line-height: 21px;
  }
  .tagline__channel { color: var(--green); font-size: 22px; }
</style>
</head>
<body>

<section class="card card--front">
  <svg class="front-waves" viewBox="0 0 806 460" preserveAspectRatio="none" aria-hidden="true">
    <rect width="806" height="460" fill="var(--navy)"/>
    <path d="M0,118 C150,52 320,70 410,128 C530,195 660,200 806,168 L806,460 L0,460 Z" fill="var(--white)"/>
    <path d="M0,24 C200,0 330,45 430,105 C560,180 700,190 806,158 L806,168 C690,200 560,198 430,130 C330,76 180,46 0,64 Z"
          fill="var(--green)" stroke="var(--white)" stroke-width="3"/>
  </svg>

  <div class="holder">
    <div class="holder__name">DALE HOLLISTER</div>
    <div class="holder__role">President</div>
  </div>

  <div class="brand">
    <span class="brand__dot"></span>
    <span class="brand__name">Corvane<br>Paintless Dent Removal</span>
  </div>

  <div class="divider"></div>

  <ul class="contacts">
    <li>
      <svg viewBox="0 0 10 10"><path d="M2 0.5 L3.8 2.6 L2.9 3.7 Q3.9 5.9 6.2 7.1 L7.3 6.2 L9.5 8 L8.3 9.5 Q2.5 8.5 0.5 1.7 Z" fill="var(--navy)"/></svg>
      631-555-0148
    </li>
    <li>
      <svg viewBox="0 0 10 10"><rect x="0.7" y="2" width="8.6" height="6" fill="none" stroke="var(--navy)" stroke-width="1.2"/><path d="M0.7 2 L5 5.5 L9.3 2" fill="none" stroke="var(--navy)" stroke-width="1.2"/></svg>
      corvanepdr@mailbox-example.com
    </li>
    <li>
      <svg viewBox="0 0 10 10"><circle cx="5" cy="5" r="4.2" fill="none" stroke="var(--navy)" stroke-width="1"/><ellipse cx="5" cy="5" rx="1.8" ry="4.2" fill="none" stroke="var(--navy)" stroke-width="0.9"/><path d="M0.8 5 H9.2" stroke="var(--navy)" stroke-width="0.9"/></svg>
      www.corvanepdr.example
    </li>
  </ul>

  <address class="address">PO Box 518<br>Brookmere, NY 11962</address>
</section>

<section class="card card--back">
  <div class="brand">
    <span class="brand__dot"></span>
    <span class="brand__name">Corvane<br>Paintless Dent Removal</span>
  </div>
  <p class="tagline">
    <span class="tagline__channel">vidstream</span> corvane paintless dent removal<br>
    25 years of experience removing Dents, Dings and Hail Damage
  </p>
</section>

</body>
</html>
```